holloway paving service

Needs to have phone number 0418259730 and email markholloway@brightmail.com.au.
ABN 62318470915
name mark holloway

For all your concreting solutions
Excavation
Exposed & colour concrete
House & shed slabs
Driveways
Landing & steps

Contact Information for Business Card

ph 0418259730
email markholloway@brightmail.com.au.
ABN 62318470915
name mark holloway

```html
<!DOCTYPE html>
<html lang="en">
<head>
<meta charset="utf-8">
<title>Holloway Paving Service – Business Card</title>
<link href="https://fonts.googleapis.com/css2?family=Roboto:wght@400;500&family=Montserrat:wght@600&display=swap" rel="stylesheet">
<style>
  :root {
    --stage: #2b2b2b;
    --orange: #f26a22;
    --slate: #666666;
    --paper: #efefef;
    --white: #ffffff;
  }
  * { box-sizing: border-box; margin: 0; padding: 0; }
  html, body { width: 1200px; height: 960px; overflow: hidden; background: var(--stage); }
  .stage { position: relative; width: 1200px; height: 960px; }

  .card { position: absolute; width: 600px; height: 342px; overflow: hidden; }
  .card--front { left: 322px; top: 110px; background: var(--paper); }
  .card--back { left: 320px; top: 493px; background: var(--orange); }

  .card__bands { position: absolute; inset: 0; }

  .contact { position: absolute; left: 31px; top: 38px; color: var(--white); font-family: "Roboto", sans-serif; }
  .contact__name { font-weight: 500; font-size: 21px; letter-spacing: 0.2px; margin-bottom: 14px; }
  .contact__line { display: flex; align-items: center; gap: 8px; font-size: 14px; line-height: 19px; }
  .contact__line svg { width: 12px; height: 12px; flex: none; }

  .services { position: absolute; left: 34px; top: 203px; color: var(--white); font-family: "Roboto", sans-serif; font-size: 14.5px; line-height: 18.2px; }
  .services__abn { margin-bottom: 2px; }
  .services__list { list-style: none; }
  .services__list li { display: flex; align-items: center; gap: 7px; }
  .services__list li::before { content: ""; width: 5px; height: 5px; background: var(--white); transform: rotate(45deg); margin-left: 1px; }

  .brand { position: absolute; left: 379px; top: 138px; border-left: 1.5px solid var(--orange); padding: 8px 0 8px 8px; font-family: "Montserrat", sans-serif; font-weight: 600; color: var(--orange); font-size: 13.5px; line-height: 16px; }
  .brand__phone { font-family: "Roboto", sans-serif; font-size: 12px; letter-spacing: 1px; margin-top: 2px; color: var(--orange); }

  .back-brand { position: absolute; right: 36px; top: 234px; text-align: center; color: var(--white); }
  .back-brand__name { font-family: "Montserrat", sans-serif; font-weight: 600; font-size: 17px; line-height: 18px; }
  .back-brand__sub { display: flex; align-items: center; gap: 10px; font-family: "Montserrat", sans-serif; font-weight: 600; font-size: 15px; letter-spacing: 2px; line-height: 18px; }
  .back-brand__sub::before, .back-brand__sub::after { content: ""; flex: 1; height: 2px; background: var(--white); }
  .back-brand__phone { font-family: "Roboto", sans-serif; font-size: 15px; letter-spacing: 1.5px; line-height: 17px; }
  .back-brand__web { font-family: "Roboto", sans-serif; font-size: 14px; letter-spacing: 3.6px; margin-top: 3px; }
</style>
</head>
<body>
<main class="stage">

  <section class="card card--front" aria-label="Business card front">
    <svg class="card__bands" viewBox="0 0 600 342" aria-hidden="true">
      <polygon points="0,0 348,0 238,164 0,164" fill="#f26a22"/>
      <polygon points="0,170 240,170 368,342 0,342" fill="#666666"/>
    </svg>

    <div class="contact">
      <h1 class="contact__name">MARK HOLLOWAY</h1>
      <p class="contact__line">
        <svg viewBox="0 0 12 12"><path d="M2.5 1 L4.5 1 L5.3 3.4 L4 4.4 Q5 6.8 7.6 8 L8.6 6.7 L11 7.5 L11 9.5 Q10.5 11 9 11 Q1 10 1 3 Q1 1.5 2.5 1 Z" fill="#fff"/></svg>
        0418259730
      </p>
      <p class="contact__line">
        <svg viewBox="0 0 12 12"><rect x="1" y="2.5" width="10" height="7" fill="#fff"/><path d="M1 2.5 L6 6.5 L11 2.5" stroke="#f26a22" stroke-width="1" fill="none"/></svg>
        markholloway@brightmail.com.au
      </p>
      <p class="contact__line">
        <svg viewBox="0 0 12 12"><circle cx="6" cy="6" r="5" fill="#fff"/><path d="M1 6 H11 M6 1 Q3 6 6 11 M6 1 Q9 6 6 11" stroke="#f26a22" stroke-width="0.8" fill="none"/></svg>
        www.hollowaypaving.com.au
      </p>
    </div>

    <div class="services">
      <p class="services__abn">ABN 62318470915</p>
      <ul class="services__list">
        <li>Excavation</li>
        <li>Exposed &amp; colour concrete</li>
        <li>House &amp; shed slabs</li>
        <li>Driveways</li>
        <li>Landing &amp; steps</li>
      </ul>
    </div>

    <div class="brand">
      <p>HOLLOWAY PAVING<br>SERVICE</p>
      <p class="brand__phone">0418259730</p>
    </div>
  </section>

  <section class="card card--back" aria-label="Business card back">
    <div class="back-brand">
      <p class="back-brand__name">HOLLOWAY PAVING</p>
      <p class="back-brand__sub">SERVICE</p>
      <p class="back-brand__phone">0418259730</p>
      <p class="back-brand__web">www.hollowaypaving.com.au</p>
    </div>
  </section>

</main>
</body>
</html>
```